Business card design needed

I would like a one sided black business card with the information provided above. Refer to my website www.brightvolleyracquets.com.au for an example of colors I have used for my site, would like to keep this consistent for my business cards also, I will upload my logo below.

I am a new small business that provides tennis customers with racquet re stringing, tennis strings and accessories.

Industry/Entity Type

Small Business

Contact Information for Business Card

Bright Volley Tennis

Owen Whitby
Managing Director

brightvolleyracquets@mailbox.example
www.brightvolleyracquets.com.au
0491 726 305

Racquet Restringing/Tennis Strings/Accessories

Requirements
Must have
• Must have my logo and card must be black

```html
<!DOCTYPE html>
<html lang="en">
<head>
<meta charset="utf-8">
<title>Bright Volley Tennis – Business Card</title>
<link rel="stylesheet" href="https://fonts.googleapis.com/css2?family=Questrial&family=Michroma&display=swap">
<style>
  :root {
    --backdrop: #ecebe8;
    --card-black: #000000;
    --lime: #b6d334;
    --court-blue: #2c4b80;
    --deep-blue: #1c3568;
    --white: #ffffff;
    --rule: #8a8a8a;
  }
  * { margin: 0; padding: 0; box-sizing: border-box; }
  html, body {
    width: 1200px; height: 475px; overflow: hidden;
    background: var(--backdrop);
    font-family: "Questrial", "Helvetica Neue", Arial, sans-serif;
  }
  .stage { position: relative; width: 1200px; height: 475px; }

  .card {
    position: absolute;
    width: 547px; height: 313px;
    background: var(--card-black);
    border-radius: 0 26px 0 26px;
    overflow: hidden;
    color: var(--white);
  }
  .card--front { left: 31px; top: 81px; }
  .card--back  { left: 607px; top: 86px; }

  .brand {
    position: absolute;
    display: flex; flex-direction: column; align-items: center;
  }
  .brand__ball {
    width: 46px; height: 46px; border-radius: 50%;
    background: var(--lime);
    margin-bottom: 12px;
  }
  .brand__name {
    font-family: "Michroma", "Questrial", sans-serif;
    font-size: 21px; letter-spacing: 1px;
    color: var(--lime);
    text-transform: uppercase;
    white-space: nowrap;
  }
  .card--front .brand { left: 0; right: 0; top: 38px; }
  .card--back .brand  { left: 0; right: 0; top: 74px; }

  .person {
    position: absolute; left: 88px; top: 180px;
    color: var(--lime);
  }
  .person__name { font-size: 18px; letter-spacing: 0.5px; text-transform: uppercase; }
  .person__title { font-size: 14px; margin-top: 2px; }

  .divider {
    position: absolute; left: 253px; top: 182px;
    width: 1px; height: 40px; background: var(--rule);
  }

  .contact {
    position: absolute; left: 268px; top: 181px;
    font-size: 12.5px; line-height: 20px; letter-spacing: 0.2px;
    list-style: none; white-space: nowrap;
  }

  .wave-band {
    position: absolute; left: 0; bottom: 0;
    width: 547px; height: 68px;
    background: linear-gradient(180deg, var(--deep-blue), var(--court-blue));
  }

  .web {
    position: absolute;
    font-size: 13.5px; letter-spacing: 0.4px;
    color: var(--white);
  }
  .card--front .web { right: 28px; bottom: 22px; }
  .card--back .web { left: 0; right: 0; top: 236px; text-align: center; letter-spacing: 1.6px; font-size: 14px; }
</style>
</head>
<body>
<main class="stage">

  <section class="card card--front" aria-label="Business card front">
    <div class="wave-band" role="img" aria-label="Decorative blue and lime wave band along the bottom edge"></div>

    <div class="brand">
      <span class="brand__ball"></span>
      <span class="brand__name">Bright Volley Tennis</span>
    </div>

    <div class="person">
      <p class="person__name">Owen Whitby</p>
      <p class="person__title">Managing Director</p>
    </div>
    <span class="divider"></span>
    <ul class="contact">
      <li>P : 0491 726 305</li>
      <li>E : brightvolleyracquets@mailbox.example</li>
    </ul>

    <p class="web">www.brightvolleyracquets.com.au</p>
  </section>

  <section class="card card--back" aria-label="Business card back">
    <div class="brand">
      <span class="brand__ball"></span>
      <span class="brand__name">Bright Volley Tennis</span>
    </div>
    <p class="web">www.brightvolleyracquets.com.au</p>
  </section>

</main>
</body>
</html>
```